Website for new crypto research organization

See brief (attached). This is a pretty basic website with only a handful of pages + ability to collect email addresses.

```html
<!DOCTYPE html>
<html lang="en">
<head>
<meta charset="utf-8">
<title>Tealwave Research</title>
<link href="https://fonts.googleapis.com/css2?family=Lato:wght@400;700;900&display=swap" rel="stylesheet">
<style>
:root{
  --teal:#16998c;
  --blue:#1b92cf;
  --ink:#1d1d1d;
  --text:#333;
  --line:#b9c2c8;
  --panel:#e4e8f0;
  --white:#fff;
}
*{box-sizing:border-box;margin:0;padding:0}
html,body{width:1200px;height:2774px;overflow:hidden}
body{font-family:"Lato",sans-serif;color:var(--text);background:var(--white);position:relative}
a{color:inherit;text-decoration:none}

.site-header{height:120px;position:relative}
.brand{position:absolute;left:77px;top:38px;display:flex;align-items:center;gap:10px;font-weight:900;font-size:24px;color:var(--teal);letter-spacing:.5px}
.brand-mark{width:26px;height:26px;background:var(--teal)}
.main-nav{position:absolute;right:72px;top:50px;display:flex;gap:0}
.main-nav a{font-weight:900;font-size:15px;color:var(--ink);margin-left:30px;position:relative}
.main-nav a:nth-child(4){margin-left:38px}
.main-nav a:nth-child(5){margin-left:38px}
.main-nav a:nth-child(6){margin-left:38px}
.main-nav a.active{color:var(--teal)}
.main-nav a.active::after{content:"";position:absolute;left:-7px;right:-7px;top:31px;height:2px;background:var(--teal)}

.hero{height:635px;position:relative;text-align:center;color:var(--white)}
.hero-photo{position:absolute;inset:0;background:linear-gradient(90deg,#3b3f52 0%,#5d5e66 30%,#8a8a8c 50%,#6a4e5a 70%,#5a4a3a 100%)}
.hero-photo::after{content:"";position:absolute;inset:0;background:rgba(20,20,30,.35)}
.hero-content{position:relative;padding-top:120px}
.hero h1{font-weight:900;font-size:82px;line-height:86px;letter-spacing:1px;text-shadow:0 2px 6px rgba(0,0,0,.4)}
.hero p{font-size:29px;line-height:41px;margin-top:8px;text-shadow:0 2px 4px rgba(0,0,0,.5)}
.btn{display:inline-block;background:var(--blue);color:var(--white);font-weight:900;text-transform:uppercase}
.hero .btn{margin-top:25px;width:281px;height:57px;line-height:57px;font-size:18px}
.dots{position:absolute;left:0;right:0;top:572px;display:flex;justify-content:center;gap:12px}
.dots span{width:14px;height:14px;border-radius:50%;background:var(--white)}
.dots span.on{background:#4c8de0}

.section-title{display:flex;align-items:center;justify-content:center;gap:22px;font-weight:900;color:var(--teal);text-transform:uppercase}
.section-title::before,.section-title::after{content:"";width:88px;height:1px;background:var(--line)}

.about{height:483px;text-align:center;padding-top:52px}
.about .section-title{font-size:42px}
.about p{width:880px;margin:22px auto 0;font-size:18px;line-height:35px;color:#222}
.about .btn{margin-top:50px;width:208px;height:57px;line-height:57px;font-size:18px}

.process{height:580px;display:flex}
.process-intro{width:587px;position:relative;color:var(--white);text-align:center}
.process-photo{position:absolute;inset:0;background:linear-gradient(135deg,#1c8f86 0%,#25b08a 45%,#1a8d9b 100%)}
.process-copy{position:relative;padding:176px 32px 0}
.process-copy h2{font-weight:900;font-size:42px;line-height:42px;text-transform:uppercase;position:relative}
.process-copy h2::before{content:"";position:absolute;left:43px;top:44px;width:75px;height:1px;background:rgba(255,255,255,.6)}
.process-copy h2::after{content:"";position:absolute;right:8px;top:44px;width:75px;height:1px;background:rgba(255,255,255,.6)}
.process-copy p{font-size:19px;line-height:35px;margin-top:14px}
.process-grid{flex:1;background:var(--panel);display:grid;grid-template-columns:243px 243px;grid-auto-rows:189px;gap:26px 26px;padding:89px 0 0 27px}
.service{background:var(--white);text-align:center;padding-top:28px}
.service svg{width:72px;height:72px;stroke:var(--blue);fill:none;stroke-width:2}
.service h3{font-weight:900;font-size:19px;line-height:25px;color:var(--ink);text-transform:uppercase;margin-top:12px}

.news{height:510px;position:relative;padding-top:60px}
.news .section-title{font-size:42px}
.news .section-title::before,.news .section-title::after{width:75px;margin:0 20px}
.news-list{position:absolute;left:75px;top:142px;display:flex;gap:30px}
.news-card{width:330px;height:296px;border:1px solid #aeb4b8}
.news-date{height:48px;line-height:46px;border-bottom:1px solid #aeb4b8;padding-left:16px;font-size:18px;color:#222}
.news-body{padding:16px 16px 0}
.news-body h3{font-weight:900;font-size:19px;line-height:28px;color:var(--blue);text-transform:uppercase}
.news-body p{font-size:17px;line-height:29px;margin-top:10px;color:#222}
.news-body a{display:block;font-weight:900;font-size:15px;margin-top:12px;color:var(--ink)}
.arrow{position:absolute;top:262px;width:16px;height:26px}
.arrow svg{width:16px;height:26px;stroke:#333;stroke-width:3;fill:none}
.arrow.prev{left:46px}
.arrow.next{left:1139px}

.subscribe{height:246px;background:linear-gradient(90deg,#17999a 0%,#1b92cf 100%);text-align:center;padding-top:66px}
.subscribe .section-title{color:var(--white);font-size:35px}
.subscribe .section-title::before,.subscribe .section-title::after{width:75px;background:rgba(255,255,255,.7)}
.subscribe-form{display:flex;justify-content:center;gap:16px;margin-top:24px}
.subscribe-form input{width:262px;height:43px;border:none;padding-left:14px;font-family:"Lato",sans-serif;font-size:14px;color:#555;background:var(--white)}
.subscribe-form button{margin-left:-4px;width:89px;height:43px;border:none;background:#121418;color:var(--white);font-family:"Lato",sans-serif;font-weight:900;font-size:15px}

.site-footer{height:200px;text-align:center;padding-top:52px}
.footer-nav{display:flex;justify-content:center;gap:37px}
.footer-nav a{font-weight:900;font-size:15px;color:var(--ink)}
.copyright{font-size:14px;margin-top:24px;color:#222}
.social{display:flex;justify-content:center;gap:20px;margin-top:22px}
.social span{width:22px;height:22px;border-radius:50%;background:#222}
</style>
</head>
<body>

<header class="site-header">
  <div class="brand"><span class="brand-mark"></span>TEALWAVE RESEARCH</div>
  <nav class="main-nav">
    <a href="#" class="active">HOME</a>
    <a href="#">ABOUT US</a>
    <a href="#">RESEARCH</a>
    <a href="#">NEWS</a>
    <a href="#">CAREERS</a>
    <a href="#">CONTACT US</a>
  </nav>
</header>

<section class="hero">
  <div class="hero-photo" role="img" aria-label="Photo of a narrow city alley with graffiti-covered walls"></div>
  <div class="hero-content">
    <h1>WELCOME TO<br>TEALWAVE RESEARCH</h1>
    <p>We are very small startup research organization focused<br>on crypto / digital assets.</p>
    <a href="#" class="btn">Recent Research Report</a>
  </div>
  <div class="dots"><span class="on"></span><span></span><span></span><span></span></div>
</section>

<section class="about">
  <h2 class="section-title">About Comany</h2>
  <p>Lorem ipsum dolor sit amet, consectetur adipiscing elit. Vestibulum elit neque, consectetur sed porttitor eget, fringilla consequat neque. Nam vitae nisl a ex molestie accumsan. Integer eget tortor dapibus quam volutpat malesuada. Praesent euismod suscipit felis a placerat. Proin ut nunc nulla. Nam vulputate justo vitae aliquam semper. Suspendisse auctor dui a augue tempor cursus. Nullam vitae ipsum eu turpis blandit semper eu et felis.</p>
  <a href="#" class="btn">Read More</a>
</section>

<section class="process">
  <div class="process-intro">
    <div class="process-photo" role="img" aria-label="Teal-tinted photo of a person walking past a painted brick wall"></div>
    <div class="process-copy">
      <h2>Our Research<br>Process</h2>
      <p>Lorem ipsum dolor sit amet, consectetur adipiscing elit. Vestibulum elit neque, consectetur sed porttitor eget, fringilla consequat neque. Nam vitae nisl a ex molestie accumsan. Integer eget tortor...</p>
    </div>
  </div>
  <div class="process-grid">
    <div class="service">
      <svg viewBox="0 0 72 72"><circle cx="36" cy="26" r="14"/><path d="M8 68h58M14 68V50M22 68V44M30 68V48M44 68V46M52 68V40M60 68V34"/><path d="M32 20h6a3 3 0 0 1 0 6h-6zM32 26h7a3 3 0 0 1 0 6h-7zM32 18v16"/></svg>
      <h3>Crypto Digital<br>Assets</h3>
    </div>
    <div class="service">
      <svg viewBox="0 0 72 72"><rect x="24" y="4" width="26" height="16" rx="2"/><circle cx="20" cy="32" r="6"/><circle cx="52" cy="32" r="6"/><path d="M10 50h52M18 50v16M54 50v16M36 50v18M8 48c0-6 4-10 12-10M64 48c0-6-4-10-12-10"/></svg>
      <h3>Consulting<br>Process</h3>
    </div>
    <div class="service">
      <svg viewBox="0 0 72 72"><rect x="4" y="6" width="26" height="18" rx="3"/><rect x="36" y="12" width="30" height="18" rx="3"/><circle cx="26" cy="42" r="6"/><circle cx="54" cy="42" r="6"/><path d="M14 62c0-8 5-12 12-12s12 4 12 12M42 62c0-8 5-12 12-12s12 4 12 12M4 66h64"/></svg>
      <h3>Speaking<br>Process</h3>
    </div>
    <div class="service">
      <svg viewBox="0 0 72 72"><rect x="4" y="4" width="54" height="44" rx="2"/><path d="M4 12h54"/><circle cx="18" cy="30" r="8"/><path d="M36 38V26M42 38V22M48 38V30"/><circle cx="46" cy="48" r="11"/><path d="M54 56l12 12"/></svg>
      <h3>Research<br>Projects</h3>
    </div>
  </div>
</section>

<section class="news">
  <h2 class="section-title">Latest News</h2>
  <a href="#" class="arrow prev" aria-label="Previous"><svg viewBox="0 0 16 26"><path d="M13 3L4 13l9 10"/></svg></a>
  <div class="news-list">
    <article class="news-card">
      <div class="news-date">Feb10, 2022</div>
      <div class="news-body">
        <h3>Lorem ipsum dolor sit<br>amet porro</h3>
        <p>Consectetur adipiscing elit neque, sed porttitor eget, fringilla consequat neque. Nam vitae nisl a ex molestie accumsan...”</p>
        <a href="#">READ MORE</a>
      </div>
    </article>
    <article class="news-card">
      <div class="news-date">Feb10, 2022</div>
      <div class="news-body">
        <h3>Lorem ipsum dolor sit<br>amet porro</h3>
        <p>Consectetur adipiscing elit neque, sed porttitor eget, fringilla consequat neque. Nam vitae nisl a ex molestie accumsan...”</p>
        <a href="#">READ MORE</a>
      </div>
    </article>
    <article class="news-card">
      <div class="news-date">Feb10, 2022</div>
      <div class="news-body">
        <h3>Lorem ipsum dolor sit<br>amet porro</h3>
        <p>Consectetur adipiscing elit neque, sed porttitor eget, fringilla consequat neque. Nam vitae nisl a ex molestie accumsan...”</p>
        <a href="#">READ MORE</a>
      </div>
    </article>
  </div>
  <a href="#" class="arrow next" aria-label="Next"><svg viewBox="0 0 16 26"><path d="M3 3l9 10-9 10"/></svg></a>
</section>

<section class="subscribe">
  <h2 class="section-title">Email Subscribe</h2>
  <form class="subscribe-form">
    <input type="text" placeholder="Enter Name">
    <input type="email" placeholder="Enter Email Address">
    <button type="button">SIGN UP</button>
  </form>
</section>

<footer class="site-footer">
  <nav class="footer-nav">
    <a href="#">HOME</a>
    <a href="#">ABOUT US</a>
    <a href="#">RESEARCH</a>
    <a href="#">NEWS</a>
    <a href="#">CAREERS</a>
    <a href="#">CONTACT US</a>
  </nav>
  <p class="copyright">Copyright © 2022 Company Name .All Right Reserved</p>
  <div class="social" aria-label="Social links"><span></span><span></span><span></span><span></span><span></span></div>
</footer>

</body>
</html>
```